Brellwick Partners, LLC Stationary

Brellwick Partners, LLC is a new financial planning and consulting company. We are looking for designs on business cards, letterhead, envelopes, and anything else that would be useful. Our preference for business card design is two sided. We are looking for a professional and clean look with incorporating the logo and patriotic feel. Thank you to all who participate and good luck!

```html
<!DOCTYPE html>
<html lang="en">
<head>
<meta charset="utf-8">
<title>Brellwick Partners, LLC — Business Card</title>
<link href="https://fonts.googleapis.com/css2?family=Arimo:wght@400;700&display=swap" rel="stylesheet">
<style>
  :root {
    --navy: #1d3d68;
    --navy-light: #2c5687;
    --red: #c8202c;
    --red-deep: #8e1620;
    --white: #ffffff;
    --ink: #3a3a3a;
    --grey: #6b6b6b;
    --backdrop: #e9e6e1;
  }
  * { box-sizing: border-box; margin: 0; padding: 0; }
  html, body { width: 1200px; height: 950px; overflow: hidden; }
  body {
    background: var(--backdrop);
    font-family: "Arimo", Arial, sans-serif;
    position: relative;
  }
  .card {
    position: absolute;
    left: 240px;
    width: 720px;
    height: 411px;
    border-radius: 4px;
    overflow: hidden;
    box-shadow: 0 6px 18px rgba(0,0,0,.18);
  }
  /* Back side */
  .card-back {
    top: 40px;
    background: linear-gradient(135deg, var(--red) 0%, #b51b27 55%, var(--red-deep) 100%);
    color: var(--white);
  }
  .card-back .brand {
    position: absolute;
    top: 140px; left: 0; right: 0;
    text-align: center;
  }
  .brand-name {
    font-weight: 700;
    font-size: 40px;
    letter-spacing: 2px;
    text-transform: uppercase;
  }
  .brand-name .mark {
    display: inline-block;
    width: 22px; height: 22px;
    margin-right: 14px;
    vertical-align: 2px;
    background: currentColor;
  }
  .brand-tagline {
    margin-top: 8px;
    font-size: 12px;
    letter-spacing: 3px;
    text-transform: uppercase;
  }
  .card-back .site {
    position: absolute;
    bottom: 70px; left: 0; right: 0;
    text-align: center;
    font-size: 17px;
    letter-spacing: 4px;
  }
  /* Front side */
  .card-front {
    top: 500px;
    background: var(--white);
  }
  .card-front .swoosh { position: absolute; inset: 0; }
  .card-front .holder {
    position: absolute;
    top: 118px; right: 36px;
    text-align: right;
    color: var(--white);
  }
  .holder-name { font-weight: 700; font-size: 22px; letter-spacing: 1px; }
  .holder-title { font-size: 18px; letter-spacing: 1px; margin-top: 4px; }
  .card-front .brand {
    position: absolute;
    top: 96px; left: 40px;
    color: var(--navy);
    display: flex;
    align-items: flex-start;
    gap: 12px;
  }
  .card-front .brand .mark {
    width: 20px; height: 20px;
    margin-top: 6px;
    background: var(--red);
    flex: none;
  }
  .card-front .brand-name {
    font-size: 28px;
    line-height: 32px;
    letter-spacing: 1.5px;
  }
  .card-front .brand-name span { display: block; }
  .card-front .brand-tagline {
    font-size: 10px;
    color: var(--red);
    letter-spacing: 2.5px;
    margin-top: 8px;
  }
  .contact {
    position: absolute;
    top: 228px; left: 40px;
    list-style: none;
    color: var(--ink);
    font-size: 17px;
    line-height: 25px;
  }
  .contact li { display: flex; align-items: center; gap: 8px; }
  .contact svg { width: 16px; height: 16px; fill: var(--navy); flex: none; }
  .address {
    position: absolute;
    right: 60px; bottom: 34px;
    text-align: left;
    color: var(--grey);
    font-size: 17px;
    line-height: 25px;
  }
  .address .site { letter-spacing: 3px; }
</style>
</head>
<body>

  <section class="card card-back" aria-label="Business card, back">
    <div class="brand">
      <div class="brand-name"><span class="mark"></span>Brellwick Partners, LLC</div>
      <div class="brand-tagline">Financial Planning and Consulting</div>
    </div>
    <div class="site">www.brellwickpartners.com</div>
  </section>

  <section class="card card-front" aria-label="Business card, front">
    <svg class="swoosh" viewBox="0 0 720 411" preserveAspectRatio="none" aria-hidden="true">
      <defs>
        <linearGradient id="navyBand" x1="0" y1="0" x2="1" y2="0">
          <stop offset="0" stop-color="#1d3d68"/>
          <stop offset="1" stop-color="#2c5687"/>
        </linearGradient>
      </defs>
      <path d="M20,0 H720 V312 C560,172 300,50 20,0 Z" fill="#c8202c"/>
      <path d="M44,0 H720 V294 C560,156 310,38 44,0 Z" fill="url(#navyBand)"/>
    </svg>

    <div class="holder">
      <div class="holder-name">MARCUS HALE</div>
      <div class="holder-title">PRESIDENT</div>
    </div>

    <div class="brand">
      <div class="mark"></div>
      <div>
        <div class="brand-name"><span>Brellwick</span><span>Partners, LLC</span></div>
        <div class="brand-tagline">Financial Planning and Consulting</div>
      </div>
    </div>

    <ul class="contact">
      <li><svg viewBox="0 0 16 16"><path d="M3 2h3l1 3-2 1.5a8 8 0 0 0 4.5 4.5L11 9l3 1v3a1 1 0 0 1-1 1A12 12 0 0 1 2 3a1 1 0 0 1 1-1z"/></svg>555 0142 7731</li>
      <li><svg viewBox="0 0 16 16"><path d="M4 1h8v4H4z M2 6h12v7H2z M4 14h8v1H4z"/></svg>555 0198 2264</li>
      <li><svg viewBox="0 0 16 16"><path d="M1 3h14v10H1z M1 3l7 6 7-6" fill="none" stroke="#1d3d68" stroke-width="1.6"/></svg>marcus@brellwickpartners.com</li>
    </ul>

    <div class="address">
      <div>2170 Harlow Avenue</div>
      <div>Kestrel Bay, NY 10999</div>
      <div class="site">www.brellwickpartners.com</div>
    </div>
  </section>

</body>
</html>
```